business card deign

Logo needs the following on it.
1. attached logo
2. Tagline - "If it keeps a drink cold or the party going...we do it!"
3. Name- Dalton Pikes, Founder and CPO
4. Address - 412 E. Carver Avenue, Ste 2207, Tampa, FL. 33917
5. Phone - 555.318.4726

```html
<!DOCTYPE html>
<html lang="en">
<head>
<meta charset="utf-8">
<title>Talven — Business Card</title>
<link rel="stylesheet" href="https://fonts.googleapis.com/css2?family=Montserrat:wght@400;700;800&display=swap">
<style>
  :root {
    --backdrop: #1c1c1f;
    --card-dark: #232228;
    --card-light: #ffffff;
    --silver: #d4d4da;
    --ink: #111111;
    --ink-soft: #2a2a2a;
  }
  * { box-sizing: border-box; margin: 0; padding: 0; }
  html, body {
    width: 1200px;
    height: 800px;
    overflow: hidden;
    background: var(--backdrop);
    font-family: "Montserrat", sans-serif;
  }
  .sheet {
    position: relative;
    width: 1200px;
    height: 800px;
  }
  .card {
    position: absolute;
    top: 137px;
    width: 300px;
    height: 525px;
    border-radius: 22px;
  }
  .card--front {
    left: 250px;
    background: var(--card-dark);
  }
  .card--back {
    left: 650px;
    background: var(--card-light);
    padding: 50px 30px 0;
    text-align: center;
    color: var(--ink);
  }

  /* Front: vertical wordmark */
  .front-mark {
    position: absolute;
    left: 50%;
    top: 50%;
    display: flex;
    align-items: center;
    gap: 22px;
    transform: translate(-50%, -50%) rotate(-90deg);
    white-space: nowrap;
  }
  .front-mark__dot {
    width: 30px;
    height: 30px;
    border-radius: 50%;
    background: var(--silver);
  }
  .front-mark__name {
    font-weight: 800;
    font-size: 40px;
    letter-spacing: 0.42em;
    color: var(--silver);
  }

  /* Back: wordmark and details */
  .back-mark {
    display: flex;
    flex-direction: column;
    align-items: center;
    gap: 18px;
  }
  .back-mark__dot {
    width: 46px;
    height: 46px;
    border-radius: 50%;
    background: var(--ink);
  }
  .back-mark__name {
    font-weight: 800;
    font-size: 30px;
    letter-spacing: 0.5em;
    margin-right: -0.5em;
  }
  .contact {
    margin-top: 40px;
  }
  .contact__name {
    font-weight: 800;
    font-size: 26px;
    line-height: 1.1;
  }
  .contact__role {
    font-weight: 400;
    font-size: 18px;
    margin-top: 4px;
  }
  .contact__address {
    font-style: normal;
    font-weight: 400;
    font-size: 17px;
    line-height: 1.3;
    color: var(--ink-soft);
    margin-top: 20px;
  }
  .contact__rule {
    width: 82px;
    height: 0;
    border: none;
    border-top: 1.5px solid var(--ink);
    margin: 16px auto 12px;
  }
  .contact__phone {
    font-weight: 400;
    font-size: 17px;
    color: var(--ink-soft);
    letter-spacing: 0.02em;
  }
  .tagline {
    position: absolute;
    left: 30px;
    right: 30px;
    bottom: 34px;
    font-weight: 700;
    font-size: 13px;
    line-height: 1.4;
    color: var(--ink);
  }
</style>
</head>
<body>
  <main class="sheet">
    <section class="card card--front" aria-label="Card front">
      <div class="front-mark">
        <span class="front-mark__dot"></span>
        <span class="front-mark__name">TALVEN</span>
      </div>
    </section>

    <section class="card card--back" aria-label="Card back">
      <div class="back-mark">
        <span class="back-mark__dot"></span>
        <span class="back-mark__name">TALVEN</span>
      </div>
      <div class="contact">
        <h1 class="contact__name">Dalton Pikes</h1>
        <p class="contact__role">Founder and CPO</p>
        <address class="contact__address">
          412 E. Carver Avenue,<br>
          Ste 2207, Tampa,<br>
          FL. 33917
        </address>
        <hr class="contact__rule">
        <p class="contact__phone">555.318.4726</p>
      </div>
      <p class="tagline">If it keeps a drink cold or the party going...we do it!</p>
    </section>
  </main>
</body>
</html>
```